Business Cards Needed for Innovative Healthcare Marketing Company

We are a marketing company focused on healthcare. Our company is all about rebranding yourself renewing your image and generating results. The phoenix stands for "reborn" or "rising" which we provide new brands for our clients we take their old brands and renew it with creativity and innovation. I am looking for a business card with color dimension. I have attached an example of a card I think has the look and feel of what I am trying to accomplish. I like that the card example has black and grey font colors, I like the font placement and the small logo, I really like the use of the colors on the right those are the colors of my logo. My logo is phoenix so maybe incorporating flames similar to that design. I would like the back a solid color maybe red with an opaque version of the logo and website. As a marketing company I am always open to creative liberty!

Target Market(s)

Doctors and business professionals.

Industry/Entity Type

Marketing

Contact Information for Business Card

Valcorne Health Care Marketing
Marla Tenwick- CEO
#(512)638-2974
email-marla@valcorne.com
website- valcorne.com

Font styles to use
Sans Serif

Colors
ec1f27
f37122
ffc214
fbed22
fbf289
f04a50

Requirements
Must have
• The logo and required information
Nice to have
• icons by the information
Should not have
• child like font

```html
<!DOCTYPE html>
<html lang="en">
<head>
<meta charset="utf-8">
<title>Valcorne Health Care Marketing – Business Card</title>
<link rel="stylesheet" href="https://fonts.googleapis.com/css2?family=Open+Sans:wght@300;400;600;700&display=swap">
<style>
  :root {
    --backdrop: #e9e4df;
    --card-white: #ffffff;
    --brand-red: #a81f22;
    --brand-deep: #9b1c1f;
    --brand-orange: #e0732a;
    --brand-amber: #f49a22;
    --logo-rust: #b8381f;
    --ink: #2f2f2f;
    --rule: #c9c9c9;
    --shadow: rgba(0,0,0,0.28);
  }
  * { margin: 0; padding: 0; box-sizing: border-box; }
  html, body {
    width: 1200px; height: 1000px; overflow: hidden;
    background: var(--backdrop);
    font-family: "Open Sans", Arial, sans-serif;
  }
  .stage { position: relative; width: 1200px; height: 1000px; }
  .card {
    position: absolute; left: 265px; width: 667px; height: 397px;
    border-radius: 22px; overflow: hidden;
    box-shadow: 0 8px 22px var(--shadow);
  }
  .card-front { top: 73px; background: var(--card-white); }
  .card-back {
    top: 532px;
    background: radial-gradient(ellipse 60% 65% at 48% 45%, var(--brand-orange) 0%, #c94a26 55%, var(--brand-deep) 100%);
  }
  .front-waves { position: absolute; left: 0; bottom: 0; width: 667px; height: 82px; }
  .wordmark {
    position: absolute; font-weight: 300; line-height: 1;
    color: var(--logo-rust);
  }
  .wordmark .wordmark-name { display: block; font-size: 50px; letter-spacing: 1px; }
  .wordmark .wordmark-tag { display: block; font-size: 17px; letter-spacing: 0.5px; margin-top: 19px; }
  .front-mark { right: 34px; top: 56px; text-align: right; }
  .back-mark {
    left: 0; right: 0; top: 150px; text-align: center; color: #fff;
  }
  .back-mark .wordmark-name { font-size: 66px; letter-spacing: 2px; }
  .back-mark .wordmark-tag { font-size: 22px; margin-top: 22px; }
  .person { position: absolute; left: 33px; top: 176px; }
  .person-name { font-size: 20px; font-weight: 700; color: var(--brand-red); letter-spacing: 0.3px; }
  .person-role { font-size: 16px; color: var(--ink); margin-top: 1px; }
  .divider { position: absolute; left: 33px; top: 238px; width: 452px; height: 1px; background: var(--rule); }
  .address { position: absolute; left: 33px; top: 251px; font-size: 16px; line-height: 24px; color: var(--ink); }
  .contact { position: absolute; right: 30px; top: 226px; text-align: right; font-size: 16px; line-height: 27px; color: var(--ink); }
  .contact-line { display: flex; justify-content: flex-end; align-items: center; gap: 8px; }
  .contact-line svg { width: 15px; height: 13px; fill: var(--brand-red); }
  .front-web { position: absolute; right: 32px; bottom: 26px; font-size: 16px; color: #fff; letter-spacing: 0.4px; }
  .back-web { position: absolute; left: 0; right: 0; bottom: 30px; text-align: center; font-size: 16px; color: #fff; letter-spacing: 0.5px; }
</style>
</head>
<body>
<main class="stage">
  <section class="card card-front" aria-label="Card front">
    <div class="wordmark front-mark">
      <span class="wordmark-name">VALCORNE</span>
      <span class="wordmark-tag">HEALTH CARE MARKETING</span>
    </div>

    <div class="person">
      <div class="person-name">MARLA TENWICK</div>
      <div class="person-role">CEO</div>
    </div>
    <div class="divider"></div>
    <div class="address">Suite 14, 8 Harwell Plaza<br>Harbridge, 14, Lower Vale</div>

    <div class="contact">
      <div class="contact-line">(512)638-2974
        <svg viewBox="0 0 16 13" aria-hidden="true"><path d="M1 4 C4 0 12 0 15 4 L12 5.5 L11 3.5 C9 2.8 7 2.8 5 3.5 L4 5.5 Z M3 6 H13 L14.5 12 H1.5 Z"/></svg>
      </div>
      <div class="contact-line">marla@valcorne.com
        <svg viewBox="0 0 16 12" aria-hidden="true"><path d="M0 0 H16 V12 H0 Z M1.5 1.5 L8 7 L14.5 1.5 Z" fill-rule="evenodd"/></svg>
      </div>
    </div>

    <svg class="front-waves" viewBox="0 0 667 82" preserveAspectRatio="none" aria-hidden="true">
      <defs>
        <linearGradient id="waveOrange" x1="0" y1="0" x2="1" y2="0">
          <stop offset="0" stop-color="#f5a023"/>
          <stop offset="0.6" stop-color="#e0762a"/>
          <stop offset="1" stop-color="#c8481f"/>
        </linearGradient>
        <linearGradient id="waveRed" x1="0" y1="0" x2="1" y2="0">
          <stop offset="0" stop-color="#9e1d20"/>
          <stop offset="0.5" stop-color="#b52a22"/>
          <stop offset="1" stop-color="#d35a24"/>
        </linearGradient>
      </defs>
      <path d="M0 0 C120 8 220 22 320 22 C420 20 520 5 667 0 L667 26 C520 20 420 26 320 32 C200 38 100 36 0 24 Z" fill="url(#waveRed)"/>
      <path d="M0 34 C120 48 240 50 340 40 C460 29 560 16 667 12 L667 82 L0 82 Z" fill="url(#waveOrange)"/>
      <path d="M0 29 C110 42 220 44 330 36 C440 28 560 18 667 14" stroke="#fff" stroke-width="3" fill="none"/>
    </svg>
    <div class="front-web">www.valcorne.com</div>
  </section>

  <section class="card card-back" aria-label="Card back">
    <div class="wordmark back-mark">
      <span class="wordmark-name">VALCORNE</span>
      <span class="wordmark-tag">HEALTH CARE MARKETING</span>
    </div>
    <div class="back-web">www.valcorne.com</div>
  </section>
</main>
</body>
</html>
```